Velk Partners Building Business Cards

We need a business card that reflects our business as "Solar Experts" in San Diego. Browse our website www.velkpartners.example our License needs to be displayed as "CSLB# 3867140" our phone number is (619) 555-0187

Save thousands on your electric bills and increase the value of your home while helping to protect the environment. Our solar installation experts will help you design the system that's right for you, using only the highest quality equipment that will look great and give you ideal performance. Our goal is to make you energy independent, and get your electric bill to 0.

Paul Osterby
(619) 555-0187
paul@velkpartners.example

Target Market(s)

Home owners in san diego looking for solar

Industry/Entity Type

Solar Energy

Contact Information for Business Card

Paul Osterby
(619) 555-0187
paul@velkpartners.example

Font styles to use
Other font styles liked:
• Use our logo font

Requirements
Must have
• License needs to be displayed as "CSLB# 3867140" our phone number is (619) 555-0187
Nice to have
• Real images of rooftop home solar in san diego
Should not have
• our business address

```html
<!DOCTYPE html>
<html lang="en">
<head>
<meta charset="utf-8">
<title>Velk Partners Building – Business Cards</title>
<link href="https://fonts.googleapis.com/css2?family=Open+Sans:wght@400;600;700&display=swap" rel="stylesheet">
<style>
  :root {
    --stage: #000000;
    --card-light: #f3f3f3;
    --card-navy: #1f3c7b;
    --navy-deep: #193569;
    --navy-soft: #27478c;
    --navy: #1e3a73;
    --ink: #2b2b2b;
    --white: #ffffff;
  }
  * { margin: 0; padding: 0; box-sizing: border-box; }
  html, body {
    width: 1200px;
    height: 900px;
    overflow: hidden;
    background: var(--stage);
    font-family: "Open Sans", Arial, sans-serif;
  }
  .stage { position: relative; width: 1200px; height: 900px; }
  .card {
    position: absolute;
    top: 200px;
    width: 310px;
    height: 502px;
    overflow: hidden;
  }
  .card-front {
    left: 265px;
    background: var(--card-light);
    border-radius: 70px 0 70px 0;
  }
  .card-back {
    left: 641px;
    width: 309px;
    background: var(--card-navy);
    border-radius: 0 70px 0 70px;
  }
  .back-decoration {
    position: absolute;
    inset: 0;
    background:
      radial-gradient(circle at 62% 58%, var(--navy-deep) 0%, var(--navy-deep) 38%, rgba(31,60,123,0) 62%),
      radial-gradient(ellipse at 75% 8%, var(--navy-soft) 0%, rgba(31,60,123,0) 45%),
      radial-gradient(ellipse at 40% 105%, var(--navy-soft) 0%, rgba(31,60,123,0) 50%);
  }
  .wordmark {
    position: absolute;
    left: 0;
    right: 0;
    text-align: center;
    font-weight: 700;
    font-size: 22px;
    line-height: 1;
    letter-spacing: -0.3px;
    white-space: nowrap;
  }
  .card-front .wordmark { top: 158px; color: var(--navy); }
  .card-back .wordmark { top: 241px; color: var(--white); }
  .holder-name {
    position: absolute;
    left: 34px;
    top: 303px;
    font-size: 16px;
    font-weight: 700;
    color: var(--navy);
    text-transform: uppercase;
  }
  .contact-list {
    position: absolute;
    left: 33px;
    top: 353px;
    list-style: none;
    font-size: 13.5px;
    color: var(--ink);
  }
  .contact-list li {
    display: flex;
    align-items: center;
    gap: 5px;
    height: 23px;
  }
  .contact-list svg { fill: var(--navy); flex: none; }
  .license {
    position: absolute;
    left: 33px;
    top: 423px;
    font-size: 14.5px;
    font-weight: 600;
    color: var(--ink);
  }
  .license .label { color: var(--navy); font-weight: 700; }
</style>
</head>
<body>
<main class="stage">
  <section class="card card-front" aria-label="Business card front">
    <p class="wordmark">Velk Partners Building</p>
    <p class="holder-name">Paul Osterby</p>
    <ul class="contact-list">
      <li>
        <svg width="12" height="12" viewBox="0 0 24 24" aria-hidden="true"><path d="M6.6 10.8a15.1 15.1 0 0 0 6.6 6.6l2.2-2.2c.3-.3.7-.4 1-.2 1.1.4 2.3.6 3.6.6.6 0 1 .4 1 1V20c0 .6-.4 1-1 1A17 17 0 0 1 3 4c0-.6.4-1 1-1h3.5c.6 0 1 .4 1 1 0 1.3.2 2.5.6 3.6.1.3 0 .7-.2 1z"/></svg>
        <span>(619) 555-0187</span>
      </li>
      <li>
        <svg width="12" height="10" viewBox="0 0 24 18" aria-hidden="true"><path d="M0 0h24v18H0z M2 2v1l10 7 10-7V2z" fill-rule="evenodd"/></svg>
        <span>paul@velkpartners.example</span>
      </li>
    </ul>
    <p class="license"><span class="label">LICENSE:</span> CSLB# 3867140</p>
  </section>

  <section class="card card-back" aria-label="Business card back">
    <div class="back-decoration" role="img" aria-label="Large faint tone-on-tone brand decoration filling the back of the card"></div>
    <p class="wordmark">Velk Partners Building</p>
  </section>
</main>
</body>
</html>
```